Website for "Nodo de Soluciones Verdantes"

We need a new web design for an enterprise dedicated to environment and energy saving engineering, based in Monterrey, Mexico.
They offer consulting services, mainly to enhance building designs, and they are also resellers for several products in the energy saving field.

The final design should be oriented to engineers and architects, and should communicate professionalism, innovation, environment care.

Here is the website of a partner enterprise, which does pretty much the same:

http://www.cirelumen.com/

Target Market(s)

mainly architects and engineers looking for solutions on energy efficiency building

Industry/Entity Type

Environment

Requirements
Must have
• Entry page must be quite graphical and intuitive, must have a "products listing" and a "projects portfolio".

```html
<!DOCTYPE html>
<html lang="en">
<head>
<meta charset="utf-8">
<title>Nodo de Soluciones Verdantes</title>
<link href="https://fonts.googleapis.com/css2?family=Roboto+Condensed:wght@400;700&family=PT+Sans:wght@400;700&display=swap" rel="stylesheet">
<style>
:root{
  --teal:#0aa3b3;
  --teal-dark:#08909f;
  --red:#df1f26;
  --text:#6b6b6b;
  --line:#d6d6d6;
  --white:#fff;
}
*{margin:0;padding:0;box-sizing:border-box}
html,body{width:1117px;height:1200px;overflow:hidden;background:var(--white)}
body{position:relative;font-family:"PT Sans",sans-serif;color:var(--text);font-size:9px;line-height:14.5px}
.abs{position:absolute}
.brand{left:168px;top:26px;display:flex;align-items:center;gap:8px}
.brand-dot{width:30px;height:30px;border-radius:50%;background:var(--teal)}
.brand-name{font-family:"Roboto Condensed",sans-serif;font-weight:700;font-size:15px;color:#4a4a4a;line-height:17px;width:150px}
.search{left:724px;top:48px;width:226px;height:21px;border:1px solid #c9c9c9;border-radius:2px;background:#f4f4f4;font-size:8px;line-height:19px;padding-left:10px;color:#555}
.search svg{position:absolute;right:7px;top:4px}
.nav{left:0;top:98px;width:1117px;height:40px;background:var(--teal)}
.nav ul{list-style:none;position:absolute;left:167px;top:0;display:flex;height:40px}
.nav li{font-family:"Roboto Condensed",sans-serif;font-size:14px;color:var(--white);line-height:40px;text-align:center}
.nav li.active{background:var(--teal-dark)}
.hero{left:167px;top:150px;width:783px;height:352px;background:linear-gradient(180deg,#1d2a44 0%,#2d3a55 35%,#6b6450 65%,#3b2a18 100%)}
.hero-caption{left:0;top:244px;width:378px;height:108px;background:rgba(20,20,20,.55);padding:14px 0 0 39px;font-family:"Roboto Condensed",sans-serif;color:var(--white)}
.hero-caption .l1{font-size:21px;line-height:26px}
.hero-caption .l2{font-size:27px;line-height:30px}
.hero-arrows{right:13px;top:313px;display:flex;gap:2px}
.hero-arrows span{width:24px;height:24px;background:var(--red);display:flex;align-items:center;justify-content:center}
h2{font-family:"Roboto Condensed",sans-serif;font-weight:400;color:var(--red);font-size:18.5px;line-height:20px}
.welcome{left:167px;top:522px;width:783px}
.welcome p{margin-top:8px;font-size:8px;line-height:14.5px}
.col{top:622px;width:236px}
.photo{display:block;height:107px;margin-top:13px}
.col p{margin-top:9px;font-size:8px;line-height:14.5px}
.btn{display:inline-block;margin-top:13px;background:var(--teal);color:var(--white);font-size:8px;height:21px;line-height:21px;padding:0 13px}
.pager{display:flex;gap:1px}
.pager span{width:21px;height:12px;background:var(--red);display:flex;align-items:center;justify-content:center}
.product{display:flex;gap:15px;padding-bottom:16px;border-bottom:1px solid var(--line);margin-top:13px}
.product + .product{border-bottom:0;margin-top:14px;padding-bottom:0}
.product .thumb{width:84px;height:69px;flex:none}
.product h3{font-size:8px;font-weight:400;color:var(--red);line-height:12px;margin-top:2px}
.product p{margin-top:5px;font-size:8px;line-height:14.5px;color:var(--text)}
.divider{left:167px;top:883px;width:783px;height:1px;background:var(--line)}
.portfolio{left:167px;top:899px;width:783px}
.items{display:flex;gap:16px;margin-top:16px}
.item{width:184px}
.item .photo{margin-top:0;height:106px}
.item h3{margin-top:11px;font-size:8.5px;font-weight:400;color:var(--teal-dark);line-height:12px}
.item p{margin-top:4px;font-size:8px;line-height:14.5px}
.footer{left:0;top:1127px;width:1117px;height:73px;background:var(--teal);color:var(--white)}
.footer-links{left:169px;top:22px;display:flex;font-size:7.5px;line-height:10px}
.footer-links span.sep{margin:0 12px}
.copy{left:169px;top:41px;font-size:7px}
.follow{left:812px;top:24px;display:flex;align-items:center;gap:6px;font-size:7px}
.follow i{width:25px;height:25px;border-radius:50%;background:#2b7fb8;display:block}
</style>
</head>
<body>
<header>
  <div class="abs brand"><span class="brand-dot"></span><span class="brand-name">Nodo de Soluciones Verdantes</span></div>
  <div class="abs search">SEARCH :
    <svg width="12" height="12" viewBox="0 0 12 12"><circle cx="5" cy="5" r="3.8" fill="none" stroke="#bbb" stroke-width="1.2"/><line x1="7.8" y1="7.8" x2="11" y2="11" stroke="#bbb" stroke-width="1.2"/></svg>
  </div>
</header>
<nav class="abs nav">
  <ul>
    <li class="active" style="width:102px">HOME</li>
    <li style="width:120px">OUR HISTORY</li>
    <li style="width:100px">PROJECTS</li>
    <li style="width:110px">SERVICES</li>
    <li style="width:90px">NEWS</li>
    <li style="width:112px">OUR TEAM</li>
    <li style="width:126px">CONTACT US</li>
  </ul>
</nav>
<section class="abs hero" role="img" aria-label="Industrial refinery lit up at dusk">
  <div class="abs hero-caption"><div class="l1">ENVIRONMENT AND</div><div class="l2">ENERGY SAVING ENGINEERING</div></div>
  <div class="abs hero-arrows">
    <span><svg width="8" height="12"><polyline points="6,1 2,6 6,11" fill="none" stroke="#f6a0a0" stroke-width="1.2"/></svg></span>
    <span><svg width="8" height="12"><polyline points="2,1 6,6 2,11" fill="none" stroke="#f6a0a0" stroke-width="1.2"/></svg></span>
  </div>
</section>
<section class="abs welcome">
  <h2>WELCOME TO NODO</h2>
  <p>Lorem Ipsum is simply dummy text of the printing and typesetting industry. Lorem Ipsum has been the industry's standard dummy text ever since the 1500s, when an unknown printer took a galley of type and scrambled it to make a type specimen book. It has survived not only five centuries, but also the leap into electronic typesetting, remaining essentially unchanged. It was popularised in the 1960s with the release of Letraset sheets containing Lorem Ipsum passages, and more recently with desktop publishing software like Aldus PageMaker including versions of Lorem Ipsum.</p>
</section>
<section class="abs col" style="left:167px">
  <h2>OUR HISTORY</h2>
  <div class="photo" role="img" aria-label="Two engineers wearing hard hats" style="background:linear-gradient(90deg,#c9a88a,#d98a3a 40%,#5a6f8c)"></div>
  <p>Lorem Ipsum is simply dummy text of the printing and typesetting industry. Lorem Ipsum has been the industry's standard dummy text ever since the 1500s, when an unknown printer took a galley of type and scrambled...</p>
  <span class="btn">READ MORE</span>
</section>
<section class="abs col" style="left:431px">
  <h2>OUR SERVICES</h2>
  <div class="photo" role="img" aria-label="Gas plant pipelines and valves" style="background:linear-gradient(180deg,#7ea0c8,#b8bfc6 50%,#8a8e92)"></div>
  <p>Lorem Ipsum is simply dummy text of the printing and typesetting industry. Lorem Ipsum has been the industry's standard dummy text ever since the 1500s, when an unknown printer took a galley of type and scrambled...</p>
  <span class="btn">READ MORE</span>
</section>
<section class="abs col" style="left:694px;width:256px">
  <div style="display:flex;justify-content:space-between;align-items:center">
    <h2>PRODUCTS LISTING</h2>
    <div class="pager">
      <span><svg width="12" height="6"><path d="M1 3H11M1 3L3.5 1M1 3L3.5 5" stroke="#fff" stroke-width=".8" fill="none"/></svg></span>
      <span><svg width="12" height="6"><path d="M1 3H11M11 3L8.5 1M11 3L8.5 5" stroke="#fff" stroke-width=".8" fill="none"/></svg></span>
    </div>
  </div>
  <div class="product">
    <div class="thumb" role="img" aria-label="Refinery towers against blue sky" style="background:linear-gradient(135deg,#2a5fa8,#9fb4c8)"></div>
    <div><h3>LOREM IPSUM IS SIMPLY DUMMY :</h3><p>Lorem Ipsum is simply dummy text of the printing and typesetting industry. Lorem Ipsum has been the industry's.</p></div>
  </div>
  <div class="product">
    <div class="thumb" role="img" aria-label="Steel pipework structure" style="background:linear-gradient(135deg,#3f5f86,#b4c2d2)"></div>
    <div><h3>LOREM IPSUM IS SIMPLY DUMMY :</h3><p>Lorem Ipsum is simply dummy text of the printing and typesetting industry. Lorem Ipsum has been the industry's.</p></div>
  </div>
  <span class="btn" style="margin-top:20px">VIEW MORE</span>
</section>
<div class="abs divider"></div>
<section class="abs portfolio">
  <div style="display:flex;justify-content:space-between;align-items:center">
    <h2>PROJECTS PORTFOLIO</h2>
    <div class="pager" style="margin-top:6px">
      <span><svg width="12" height="6"><path d="M1 3H11M1 3L3.5 1M1 3L3.5 5" stroke="#fff" stroke-width=".8" fill="none"/></svg></span>
      <span><svg width="12" height="6"><path d="M1 3H11M11 3L8.5 1M11 3L8.5 5" stroke="#fff" stroke-width=".8" fill="none"/></svg></span>
    </div>
  </div>
  <div class="items">
    <div class="item"><div class="photo" role="img" aria-label="Solar panels under the sky" style="background:linear-gradient(160deg,#dfe8f2,#3a6fa8 60%,#1f3f6a)"></div><h3>ELECTRONIC TYPESETTING, REMAINING :</h3><p>Lorem Ipsum is simply dummy text of the printing and typesetting industry...</p></div>
    <div class="item"><div class="photo" role="img" aria-label="Power station chimneys with smoke" style="background:linear-gradient(180deg,#5a6a8a,#4a4f63 60%,#b0642a)"></div><h3>ELECTRONIC TYPESETTING, REMAINING :</h3><p>Lorem Ipsum is simply dummy text of the printing and typesetting industry...</p></div>
    <div class="item"><div class="photo" role="img" aria-label="Wind turbines on green field" style="background:linear-gradient(180deg,#2a66b8,#8fbde6 60%,#5ea83a)"></div><h3>ELECTRONIC TYPESETTING, REMAINING :</h3><p>Lorem Ipsum is simply dummy text of the printing and typesetting industry...</p></div>
    <div class="item"><div class="photo" role="img" aria-label="Power line pylons at sunset" style="background:linear-gradient(180deg,#e89a1a,#f2c23a 50%,#6a3a0a)"></div><h3>ELECTRONIC TYPESETTING, REMAINING :</h3><p>Lorem Ipsum is simply dummy text of the printing and typesetting industry...</p></div>
  </div>
</section>
<footer class="abs footer">
  <div class="abs footer-links"><span>HOME</span><span class="sep">|</span><span>OUR HISTORY</span><span class="sep">|</span><span>PROJECTS</span><span class="sep">|</span><span>SERVICES</span><span class="sep">|</span><span>NEWS</span><span class="sep">|</span><span>CONTACT US</span></div>
  <div class="abs copy">COPYRIGHTS 2013 - NODO - ALL RIGHTS RESERVED</div>
  <div class="abs follow"><span>FOLLOW US :</span><i aria-label="Social link"></i><i aria-label="Social link" style="background:#3ab0e0"></i><i aria-label="Social link" style="background:#1f7590"></i></div>
</footer>
</body>
</html>
```